Support People to improve their image and well-being by provided personalised advise

We need a design for business cards that could be used for production on plano press. We build a new business in our region for advising mostly women (also men though) on style embracing several aspects including fashion, style, self-confidence and ultimately your internal and external image. The business card should be "classy", "french-style". The business is located in the french -speaking part of Switzerland, close to France. The name of the company is Lomu Grace

Target Market(s)

Service fees won't be cheap (medium to premium) thus we target mid-class to upper-class women (1st target) and men (2nd target)

Industry/Entity Type

Life Coaching

Contact Information for Business Card

Conseil en Image

+41 76 418 63 07
tovasel@lomu-grace.example
linkedin.example/in/sel-moran-tova

Logo Text

Lomu Grace

Colors

Designer to choose colors to be used in the design.

```html
<!DOCTYPE html>
<html lang="en">
<head>
<meta charset="utf-8">
<title>Lomu Grace — Business Card</title>
<link href="https://fonts.googleapis.com/css2?family=Questrial&display=swap" rel="stylesheet">
<style>
  :root {
    --backdrop: #b5b5b5;
    --card-rose: #d76a6a;
    --card-paper: #f2f2f2;
    --ink-dark: #3a3a3a;
    --accent-rose: #d75f5d;
    --text-body: #3c3c3c;
  }
  * { margin: 0; padding: 0; box-sizing: border-box; }
  html, body {
    width: 1200px;
    height: 576px;
    overflow: hidden;
    background: var(--backdrop);
    font-family: "Questrial", "Century Gothic", sans-serif;
  }
  .stage { position: relative; width: 1200px; height: 576px; }
  .card {
    position: absolute;
    top: 138px;
    border-radius: 16px;
    overflow: hidden;
  }
  .card--front {
    left: 82px;
    width: 484px;
    height: 294px;
    background: var(--card-rose);
  }
  .card--back {
    left: 602px;
    width: 481px;
    height: 291px;
    background: var(--card-paper);
  }
  .wordmark {
    position: absolute;
    color: var(--ink-dark);
    white-space: nowrap;
    font-weight: 400;
    letter-spacing: -0.5px;
  }
  .card--front .wordmark {
    left: 0;
    right: 0;
    top: 124px;
    text-align: center;
    font-size: 44px;
    line-height: 1;
  }
  .card--back .wordmark {
    left: 62px;
    top: 122px;
    font-size: 30px;
    line-height: 1;
  }
  .person {
    position: absolute;
    left: 271px;
    top: 93px;
  }
  .person__name {
    color: var(--accent-rose);
    font-size: 19.5px;
    line-height: 1;
  }
  .person__role {
    margin-top: 9px;
    color: var(--text-body);
    font-size: 11.5px;
    line-height: 1;
  }
  .contact-list {
    position: absolute;
    left: 273px;
    top: 154px;
    list-style: none;
  }
  .contact-list__item {
    display: flex;
    align-items: center;
    height: 17.6px;
    color: var(--text-body);
    font-size: 12.5px;
  }
  .contact-list__icon {
    width: 10px;
    height: 10px;
    margin-right: 14px;
    fill: var(--accent-rose);
    flex: none;
  }
</style>
</head>
<body>
<main class="stage">
  <section class="card card--front" aria-label="Card front">
    <div class="wordmark">Lomu Grace</div>
  </section>

  <section class="card card--back" aria-label="Card back">
    <div class="wordmark">Lomu Grace</div>

    <div class="person">
      <p class="person__name">Tova Sel Moran</p>
      <p class="person__role">Managing Director</p>
    </div>

    <ul class="contact-list">
      <li class="contact-list__item">
        <svg class="contact-list__icon" viewBox="0 0 10 10" aria-hidden="true">
          <path d="M1 2.2 Q5 0.4 9 2.2 L8.6 3.6 L6.8 3.2 L6.6 2.4 Q5 2 3.4 2.4 L3.2 3.2 L1.4 3.6 Z"/>
          <path d="M2.6 4.2 H7.4 L8.6 9 H1.4 Z"/>
        </svg>
        555.555.0142
      </li>
      <li class="contact-list__item">
        <svg class="contact-list__icon" viewBox="0 0 10 10" aria-hidden="true">
          <path d="M0.5 2 H9.5 V8 H0.5 Z M1.2 2.6 L5 5.6 L8.8 2.6" fill-rule="evenodd"/>
          <path d="M1 2.4 L5 5.4 L9 2.4" fill="none" stroke="#f2f2f2" stroke-width="0.8"/>
        </svg>
        tova@lomu-grace.example
      </li>
      <li class="contact-list__item">
        <svg class="contact-list__icon" viewBox="0 0 10 10" aria-hidden="true">
          <circle cx="5" cy="5" r="4.5"/>
          <g fill="none" stroke="#f2f2f2" stroke-width="0.7">
            <ellipse cx="5" cy="5" rx="1.8" ry="4.5"/>
            <line x1="0.5" y1="5" x2="9.5" y2="5"/>
            <line x1="5" y1="0.5" x2="5" y2="9.5"/>
          </g>
        </svg>
        www.lomu-grace.example
      </li>
    </ul>
  </section>
</main>
</body>
</html>
```